Quorva - corporate Business Card

We need a good look and innovative business card for a new start up company based in Los Angeles called "Quorva". We are in a payment business, including payment card, app, and ewallet. We are expert in online payment and Card not present (CNP) transaction.
We need an innovative, modern business card.

Our logo font is Aero Matics

Target Market(s)

Startup - Bank - Online Payment - Card Manufacturing

Industry/Entity Type

Startup

Contact Information for Business Card

phone: 555 014 7396 - Address: 4172 Marlowe blvd, Halden Park, OR 97214

Requirements
Must have
• Message: innovative, professional, expert, high tech, trust, online payment expert, security
Nice to have
• no comment
Should not have
• no Comment

```html
<!DOCTYPE html>
<html lang="en">
<head>
<meta charset="utf-8">
<title>Quorva – Business Card</title>
<link href="https://fonts.googleapis.com/css2?family=Source+Sans+3:wght@400;600;700&display=swap" rel="stylesheet">
<style>
  :root {
    --backdrop: #4a423d;
    --card: #0d0d0d;
    --brand-red: #c0202e;
    --ink-light: #f2f2f2;
    --divider: #2e2e2e;
  }
  * { margin: 0; padding: 0; box-sizing: border-box; }
  html, body { width: 1200px; height: 900px; overflow: hidden; }
  body {
    background: var(--backdrop);
    font-family: "Source Sans 3", Arial, sans-serif;
    position: relative;
  }
  .card {
    position: absolute;
    width: 520px;
    height: 300px;
    background: var(--card);
    border-radius: 3px;
    box-shadow: 0 18px 40px rgba(0,0,0,0.45);
    overflow: hidden;
  }
  .card--contact { left: 50px; top: 300px; }
  .card--brand { left: 630px; top: 300px; }

  /* contact side */
  .brand-disc {
    position: absolute;
    left: 62px; top: 62px;
    width: 176px; height: 176px;
    border-radius: 50%;
    background: var(--brand-red);
    display: flex; align-items: center; justify-content: center;
  }
  .brand-disc__name {
    color: var(--card);
    font-weight: 700;
    font-size: 34px;
    letter-spacing: 0.5px;
  }
  .divider {
    position: absolute;
    left: 285px; top: 40px;
    width: 1px; height: 220px;
    background: var(--divider);
  }
  .contact {
    position: absolute;
    left: 308px; top: 62px;
    color: var(--ink-light);
  }
  .contact__name {
    color: var(--brand-red);
    font-weight: 700;
    font-size: 20px;
    line-height: 1;
  }
  .contact__role {
    font-size: 14px;
    margin-top: 3px;
  }
  .contact__lines {
    list-style: none;
    margin-top: 30px;
    font-size: 14px;
  }
  .contact__lines li {
    display: flex; align-items: center; gap: 7px;
    line-height: 20px;
  }
  .contact__lines svg { width: 10px; height: 10px; fill: var(--brand-red); }
  .contact__address {
    margin-top: 18px;
    font-size: 14px;
    line-height: 20px;
  }

  /* brand side */
  .wordmark {
    position: absolute;
    left: 0; top: 0; width: 100%; height: 100%;
    display: flex; align-items: center; justify-content: center;
    gap: 14px;
  }
  .wordmark__dot {
    width: 92px; height: 92px;
    border-radius: 50%;
    background: var(--brand-red);
  }
  .wordmark__name {
    color: var(--brand-red);
    font-weight: 700;
    font-size: 62px;
    line-height: 1;
    padding-bottom: 6px;
  }
</style>
</head>
<body>
  <section class="card card--contact" aria-label="Business card, contact side">
    <div class="brand-disc"><span class="brand-disc__name">Quorva</span></div>
    <div class="divider"></div>
    <div class="contact">
      <p class="contact__name">Daniel Harrow</p>
      <p class="contact__role">Managing Director</p>
      <ul class="contact__lines">
        <li>
          <svg viewBox="0 0 10 10" aria-hidden="true"><path d="M2 0.5 L3.6 2.6 L2.7 3.6 C3.3 5 4.9 6.6 6.4 7.3 L7.4 6.4 L9.5 8 L8.3 9.5 C4.5 9 1 5.5 0.5 1.7 Z"/></svg>
          555 014 7396
        </li>
        <li>
          <svg viewBox="0 0 10 10" aria-hidden="true"><circle cx="5" cy="5" r="5"/></svg>
          www.quorva.com
        </li>
      </ul>
      <p class="contact__address">4172 Marlowe blvd,<br>Halden Park, OR 97214</p>
    </div>
  </section>

  <section class="card card--brand" aria-label="Business card, brand side">
    <div class="wordmark">
      <span class="wordmark__dot"></span>
      <span class="wordmark__name">quorva</span>
    </div>
  </section>
</body>
</html>
```